business card deign

Logo needs the following on it.
1. attached logo
2. Tagline - "If it keeps the ice cold or the fun rolling...we handle it!"
3. Name- Dalton Pikes, Founder and CPO
4. Address - 412 E. Carver Avenue, Ste 2207, Tampa, FL. 33917
5. Phone - 555.318.4726

```html
<!DOCTYPE html>
<html lang="en">
<head>
<meta charset="utf-8">
<title>Hopwell Business Card</title>
<link href="https://fonts.googleapis.com/css2?family=Roboto+Condensed:wght@400;700&family=Arimo:wght@400&display=swap" rel="stylesheet">
<style>
  :root {
    --page-bg: #d3d4d6;
    --card-dark: #161616;
    --card-light: #ffffff;
    --ink-light: #ffffff;
    --ink-dark: #111111;
  }
  html, body {
    margin: 0;
    padding: 0;
    width: 900px;
    height: 1200px;
    overflow: hidden;
    background: var(--page-bg);
  }
  .canvas {
    position: relative;
    width: 900px;
    height: 1200px;
  }
  .card {
    position: absolute;
    width: 631px;
    height: 358px;
  }
  .card-front {
    left: 134px;
    top: 215px;
    background: var(--card-dark);
  }
  .card-back {
    left: 135px;
    top: 628px;
    background: var(--card-light);
  }
  .mascot-area {
    position: absolute;
    left: 204px;
    top: 78px;
    width: 202px;
    height: 151px;
    border-radius: 6px;
    background: linear-gradient(180deg, #4a4a4a 0%, #2a2a2a 100%);
  }
  .brand-name {
    position: absolute;
    left: 0;
    right: 0;
    top: 236px;
    margin: 0;
    text-align: center;
    font-family: "Roboto Condensed", sans-serif;
    font-weight: 400;
    font-size: 46px;
    line-height: 46px;
    letter-spacing: 17px;
    padding-left: 17px;
    color: var(--ink-light);
  }
  .tagline {
    position: absolute;
    left: 0;
    right: 0;
    top: 302px;
    margin: 0;
    text-align: center;
    font-family: "Roboto Condensed", sans-serif;
    font-weight: 700;
    font-size: 17px;
    letter-spacing: 0.6px;
    color: var(--ink-light);
  }
  .identity {
    position: absolute;
    right: 333px;
    top: 148px;
    text-align: right;
    color: var(--ink-dark);
  }
  .person-name {
    margin: 0;
    font-family: "Roboto Condensed", sans-serif;
    font-weight: 700;
    font-size: 33px;
    line-height: 36px;
  }
  .person-role {
    margin: 2px 0 0;
    font-family: "Arimo", sans-serif;
    font-size: 15.5px;
    line-height: 19px;
  }
  .divider {
    position: absolute;
    left: 315px;
    top: 144px;
    width: 2px;
    height: 70px;
    background: var(--ink-dark);
  }
  .contact {
    position: absolute;
    left: 331px;
    top: 140px;
    font-family: "Arimo", sans-serif;
    color: var(--ink-dark);
  }
  .phone {
    display: flex;
    align-items: center;
    gap: 7px;
    margin: 0;
    font-size: 17.5px;
    letter-spacing: 1px;
    line-height: 20px;
  }
  .phone svg { width: 12px; height: 12px; }
  .address {
    margin: 10px 0 0;
    font-size: 14px;
    line-height: 25px;
  }
</style>
</head>
<body>
<div class="canvas">
  <section class="card card-front">
    <div class="mascot-area" role="img" aria-label="Brand mascot illustration"></div>
    <h1 class="brand-name">HOPWELL</h1>
    <p class="tagline">If it keeps the ice cold or the fun rolling...we handle it!</p>
  </section>

  <section class="card card-back">
    <div class="identity">
      <h2 class="person-name">DALTON PIKES</h2>
      <p class="person-role">Founder and CPO</p>
    </div>
    <div class="divider"></div>
    <div class="contact">
      <p class="phone">
        <svg viewBox="0 0 24 24" aria-hidden="true"><path fill="#111" d="M6.6 10.8a15.1 15.1 0 0 0 6.6 6.6l2.2-2.2c.3-.3.7-.4 1-.2 1.1.4 2.3.6 3.6.6.6 0 1 .4 1 1V20c0 .6-.4 1-1 1A17 17 0 0 1 3 4c0-.6.4-1 1-1h3.5c.6 0 1 .4 1 1 0 1.3.2 2.5.6 3.6.1.3 0 .7-.2 1z"/></svg>
        555.318.4726
      </p>
      <p class="address">412 E. Carver Avenue, Ste 2207<br>Tampa, FL. 33917</p>
    </div>
  </section>
</div>
</body>
</html>
```